Stationary Design for Quince consultant and support company

We need new stationary designed for a London based support company that provide on-site and remote support services for Quince products. Our clients are both consumers and businesses.

We would like a letterhead, compliment slip, business card and possibly an e-mail signature designed.

Business card designs can be either 1 side or 2, depending on designs we receive we may choose a preference for 1 or 2 sides later on in the design stage.

Designs needs to be at least 300dpi and should be done using CMYK colours.

We want the design to be bold, easy to read, clean and professional.

We have attached our company logo in 2 colour variations (if you need any other source files then please ask).

Our logo colours are as follows:

Blue (85, 50, 0, 0) and Green (50, 0, 100, 0)

We use two different suppliers for out stationary so here are the size dimensions for both. Unfortunately they are ever so slightly different size wise so hopefully we can get something that accommodates both, we can provide dimensions if required for final versions.

Some fonts that have been used before with our company are Probert (for tagline on our company logo) and previously had Nauman used, however we are very much open to seeing what the designers come up with and the fonts mentioned are not a requirement.
Updates

Company details for designs (however the template should be editable for multiple staff) Lumora Ltd. Registered Office: 62-70 Harrowfield Lane London N7 3QD 020 7591 3384 www.lumora-it.example info@lumora-it.example Company is Registered in England and Wales Company No. 07342519 Directors details (if you want to make the template using his details), rest of the details are as above Dan Frost Director dan@lumora-it.example

Hi all, Thank you for your submissions so far. Could we please ask that you don't use the logo with the tagline from our website for the stationary designs and only the logos provided in the design brief. For the business cards we are looking at normal rectangular business cards to be used and we can provide a template guide for size if needed, please just ask. Regards Lumora Team

Target Market(s)

Our target market are consumers (of all ages) and small/medium businesses.

Industry/Entity Type

Business

Font styles to use
Serif
Sans Serif

Requirements
Must have
• At least business card, letterhead and compliment slip submitted (we need all 3 designed this time round)
Should not have
• Business cards should not have the writing "registered office" (letterheads and compliment slips can along the bottom edge)

```html
<!DOCTYPE html>
<html lang="en">
<head>
<meta charset="utf-8">
<title>Lumora Stationery Set</title>
<link href="https://fonts.googleapis.com/css2?family=Exo+2:wght@400;600;700&family=Lora:ital@1&display=swap" rel="stylesheet">
<style>
  :root {
    --bg: #c5d1da;
    --paper: #f2f3f4;
    --paper-shade: #e6e8ea;
    --navy: #3a4d6e;
    --navy-dark: #2f4060;
    --blue: #2a7bbf;
    --green: #8ab544;
    --ink: #3b3f45;
    --muted: #7b828a;
    --on-navy: #e9edf2;
    --on-navy-soft: #cfd8e4;
  }
  * { margin: 0; padding: 0; box-sizing: border-box; }
  html, body { width: 1200px; height: 1000px; overflow: hidden; }
  body { background: var(--bg); font-family: "Exo 2", Arial, sans-serif; color: var(--ink); position: relative; }
  .piece { position: absolute; box-shadow: 0 4px 12px rgba(40,55,75,.18); }
  .wordmark { font-family: "Exo 2", Arial, sans-serif; font-weight: 700; color: var(--ink); letter-spacing: .04em; white-space: nowrap; }
  .wordmark.on-dark { color: var(--on-navy); }
  .brand-field { position: absolute; }

  /* Letterhead */
  .letterhead { left: 140px; top: 120px; width: 290px; height: 410px; background: var(--paper); }
  .letterhead .brand-field { left: 0; top: 0; width: 60px; height: 62px; background: linear-gradient(135deg, #8aa0c8 0%, #b9d18f 100%); }
  .letterhead .wordmark { position: absolute; right: 36px; top: 64px; font-size: 13px; }
  .letter-body { position: absolute; left: 52px; right: 36px; top: 100px; font-size: 4.6px; line-height: 1.6; color: var(--muted); }
  .letter-body .salutation { font-family: "Lora", Georgia, serif; font-style: italic; font-size: 7px; color: var(--ink); margin-bottom: 6px; }
  .letter-body p { margin-bottom: 10px; }
  .letter-body .signoff { font-family: "Lora", Georgia, serif; font-style: italic; font-size: 6px; color: var(--ink); text-align: right; margin-top: 12px; }
  .letter-footer { position: absolute; left: 52px; right: 36px; bottom: 16px; font-size: 3.6px; color: var(--muted); display: flex; justify-content: space-between; white-space: nowrap; }
  .letter-footer span::before { content: ""; display: inline-block; width: 3px; height: 3px; background: var(--blue); margin-right: 2px; }

  /* Envelopes and compliment slip */
  .envelope { width: 260px; height: 150px; background: var(--paper); }
  .envelope-open { left: 470px; top: 170px; }
  .envelope-open .flap { position: absolute; left: 0; top: -30px; width: 260px; height: 40px; background: var(--navy); border-radius: 6px 6px 0 0; }
  .envelope-open .flap-inner { position: absolute; left: 0; top: 10px; width: 260px; height: 34px; background: var(--navy-dark); clip-path: polygon(0 0, 100% 0, 92% 100%, 8% 100%); }

  .compliment-slip { left: 770px; top: 110px; width: 260px; height: 130px; background: var(--paper); }
  .compliment-slip .wordmark { position: absolute; left: 18px; top: 44px; font-size: 14px; }
  .return-address { position: absolute; right: 22px; top: 18px; font-size: 3.6px; line-height: 1.7; color: var(--muted); }
  .return-address span { display: block; white-space: nowrap; }
  .return-address span::before { content: ""; display: inline-block; width: 3px; height: 3px; background: var(--blue); margin-right: 2px; }

  .envelope-back { left: 770px; top: 270px; height: 130px; }
  .envelope-back .flap { position: absolute; left: 0; top: 0; width: 260px; height: 52px; background: var(--navy); clip-path: polygon(0 0, 100% 0, 100% 40%, 92% 100%, 8% 100%, 0 40%); }
  .envelope-back .wordmark { position: absolute; left: 0; right: 0; top: 18px; text-align: center; font-size: 10px; }

  /* Business cards */
  .card { width: 96px; height: 58px; background: var(--navy); top: 380px; }
  .card-front { left: 472px; }
  .card-front .wordmark { position: absolute; left: 0; right: 0; top: 22px; text-align: center; font-size: 10px; }
  .card-back { left: 590px; }
  .card-back .brand-field { left: 0; top: 0; width: 42px; height: 58px; background: linear-gradient(135deg, var(--blue) 0%, var(--green) 100%); }
  .card-details { position: absolute; left: 48px; top: 14px; font-size: 3.6px; line-height: 1.6; color: var(--on-navy-soft); white-space: nowrap; }
  .card-details .name { font-size: 5.4px; font-weight: 600; color: #fff; }
  .card-details .role { color: var(--green); margin-bottom: 3px; }

  /* Folder cover */
  .folder-cover { left: 140px; top: 560px; width: 290px; height: 410px; background: var(--navy); }
  .folder-cover .wordmark { position: absolute; right: 22px; top: 34px; font-size: 17px; }
  .folder-cover .brand-field { left: 0; top: 120px; width: 290px; height: 290px; background: linear-gradient(135deg, var(--blue) 0%, #3f7fae 55%, var(--green) 100%); opacity: .9; }

  /* Open folder */
  .folder-open { left: 480px; top: 450px; width: 560px; height: 410px; background: var(--paper); display: flex; }
  .folder-panel { position: relative; flex: 1; background: linear-gradient(180deg, var(--paper) 0%, var(--paper-shade) 100%); }
  .folder-panel + .folder-panel { border-left: 1px solid #d4d8dc; }
  .pocket { position: absolute; left: 0; right: 0; bottom: 0; height: 150px; background: var(--navy); border-radius: 22px 0 0 0; }
  .folder-panel + .folder-panel .pocket { border-radius: 0 22px 0 0; }
  .pocket .wordmark { position: absolute; right: 26px; top: 28px; font-size: 14px; }
  .pocket-details { position: absolute; right: 26px; top: 52px; font-size: 3.8px; line-height: 1.7; color: var(--on-navy-soft); width: 70px; white-space: nowrap; }
</style>
</head>
<body>

  <section class="piece letterhead">
    <div class="brand-field" role="img" aria-label="Brand colour decoration in blue and green"></div>
    <div class="wordmark">Lumora</div>
    <div class="letter-body">
      <div class="salutation">Dear Client,</div>
      <p>Thank you for choosing our team for your device support. We offer on-site and remote help for homes and offices across London, with friendly engineers ready to assist.</p>
      <p>Our plans cover setup, repairs, backups and training, so your systems stay fast, safe and simple to use every day.</p>
      <p>Please call or email us to book a visit, and we will confirm a time that suits you within one working day.</p>
      <div class="signoff">Best regards</div>
    </div>
    <div class="letter-footer">
      <span>62-70 Harrowfield Lane London N7 3QD</span>
      <span>www.lumora-it.example</span>
      <span>info@lumora-it.example</span>
      <span>020 7591 3384</span>
    </div>
  </section>

  <section class="piece envelope envelope-open">
    <div class="flap"></div>
    <div class="flap-inner"></div>
  </section>

  <section class="piece compliment-slip">
    <div class="wordmark">Lumora</div>
    <div class="return-address">
      <span>62-70 Harrowfield Lane</span>
      <span>London N7 3QD</span>
      <span>020 7591 3384</span>
      <span>info@lumora-it.example</span>
    </div>
  </section>

  <section class="piece envelope envelope-back">
    <div class="flap"></div>
    <div class="wordmark on-dark">Lumora</div>
  </section>

  <section class="piece card card-front">
    <div class="wordmark on-dark">Lumora</div>
  </section>

  <section class="piece card card-back">
    <div class="brand-field" role="img" aria-label="Brand colour decoration in blue and green"></div>
    <div class="card-details">
      <div class="name">Dan Frost</div>
      <div class="role">Director</div>
      <div>020 7591 3384</div>
      <div>dan@lumora-it.example</div>
      <div>www.lumora-it.example</div>
    </div>
  </section>

  <section class="piece folder-cover">
    <div class="wordmark on-dark">Lumora</div>
    <div class="brand-field" role="img" aria-label="Large brand colour decoration in blue and green"></div>
  </section>

  <section class="piece folder-open">
    <div class="folder-panel">
      <div class="pocket"></div>
    </div>
    <div class="folder-panel">
      <div class="pocket">
        <div class="wordmark on-dark">Lumora</div>
        <div class="pocket-details">
          62-70 Harrowfield Lane<br>
          London N7 3QD<br>
          020 7591 3384<br>
          info@lumora-it.example
        </div>
      </div>
    </div>
  </section>

</body>
</html>
```